Marlowe Group needs a business card

I would like the card to be simple but modern and elegant.
I like black and white.
or black and gold.
we are a private finance lender and also are involved in property and property developments.

please look at the business card photos i provided i would like M.G only one one side and all the other details on the other side use fonts that tie in with my theme.

Industry/Entity Type

Finance

Contact Information for Business Card

Marlowe Group (M.G) Daniel Marlowe M: 0413586207 E: danmarl@inboxmail.test

Font styles to use
Other font styles liked:
• Use fonts that would reflect our business

Colors
000000
ffffff

Requirements
Must have
• one side of details
• other side has either M.G or Marlowe Group like in the photos provided

```html
<!DOCTYPE html>
<html lang="en">
<head>
<meta charset="utf-8">
<title>Marlowe Group – Business Card</title>
<link rel="stylesheet" href="https://fonts.googleapis.com/css2?family=Open+Sans:wght@400;600;700;800&display=swap">
<style>
  :root {
    --backdrop: #e6e4e1;
    --card-white: #ffffff;
    --ink: #111111;
    --ink-soft: #555555;
    --rule: #c8c8c8;
    --band-grey: #9a9a9a;
    --card-black: #000000;
    --gold: #c9a93c;
  }
  * { box-sizing: border-box; margin: 0; padding: 0; }
  html, body {
    width: 1200px;
    height: 987px;
    overflow: hidden;
    background: var(--backdrop);
    font-family: "Open Sans", Arial, sans-serif;
  }
  .stage { position: relative; width: 1200px; height: 987px; }

  .card {
    position: absolute;
    left: 293px;
    width: 615px;
    height: 350px;
    box-shadow: 0 2px 6px rgba(0,0,0,0.25);
  }
  .card--front { top: 131px; background: var(--card-white); overflow: hidden; }
  .card--back  { top: 506px; background: var(--card-black); }

  .front__wordmark {
    position: absolute;
    left: 41px;
    top: 152px;
    width: 246px;
    text-align: center;
    font-weight: 800;
    font-size: 27px;
    letter-spacing: 1px;
    color: var(--ink);
    text-transform: uppercase;
    line-height: 1;
  }
  .front__divider {
    position: absolute;
    left: 316px;
    top: 129px;
    width: 1px;
    height: 109px;
    background: var(--rule);
  }
  .front__name {
    position: absolute;
    left: 343px;
    top: 124px;
    font-weight: 600;
    font-size: 23px;
    color: var(--ink);
    line-height: 1;
  }
  .contact-list {
    position: absolute;
    left: 347px;
    top: 170px;
    list-style: none;
  }
  .contact-list li {
    display: flex;
    align-items: center;
    height: 24px;
    font-size: 16px;
    color: var(--ink-soft);
  }
  .contact-list svg { width: 14px; height: 14px; margin-right: 10px; flex: none; }

  .front__footer-line {
    position: absolute;
    left: 0; right: 0;
    top: 320px;
    height: 3px;
    background: var(--band-grey);
  }
  .front__footer-band {
    position: absolute;
    left: 0; right: 0;
    top: 326px;
    bottom: 0;
    background: var(--card-black);
  }

  .back__monogram {
    position: absolute;
    left: 0; right: 0;
    top: 130px;
    text-align: center;
    font-weight: 800;
    font-size: 92px;
    line-height: 1;
    letter-spacing: 2px;
    color: var(--gold);
  }
</style>
</head>
<body>
<main class="stage">
  <section class="card card--front" aria-label="Card front">
    <div class="front__wordmark">Marlowe Group</div>
    <div class="front__divider"></div>
    <h1 class="front__name">Daniel Marlowe</h1>
    <ul class="contact-list">
      <li>
        <svg viewBox="0 0 14 14" aria-hidden="true"><rect x="3" y="0.5" width="8" height="13" rx="1.5" fill="none" stroke="#111" stroke-width="1.6"/><rect x="6" y="11" width="2" height="1.2" fill="#111"/></svg>
        0413586207
      </li>
      <li>
        <svg viewBox="0 0 14 14" aria-hidden="true"><rect x="0.5" y="3" width="13" height="9" fill="#111"/><path d="M0.5 3 L7 8 L13.5 3" fill="none" stroke="#fff" stroke-width="1.2"/></svg>
        danmarl@inboxmail.test
      </li>
      <li>
        <svg viewBox="0 0 14 14" aria-hidden="true"><circle cx="7" cy="7" r="6.5" fill="#111"/><ellipse cx="7" cy="7" rx="2.6" ry="6" fill="none" stroke="#fff" stroke-width="1"/><line x1="1" y1="7" x2="13" y2="7" stroke="#fff" stroke-width="1"/></svg>
        www.marlowegroup.test
      </li>
    </ul>
    <div class="front__footer-line"></div>
    <div class="front__footer-band"></div>
  </section>

  <section class="card card--back" aria-label="Card back">
    <div class="back__monogram">M.G</div>
  </section>
</main>
</body>
</html>
```